Church Website with Home Page and Member Sermon Library

I am in need of an updated design for our church website. This will include 4 pages (outlined below). We are a conservative, evangelical, Christian church. The site should be modern and clean, while still reflecting our conservative values. I already have a logo for our church, and I want the site to incorporate the logo, and match the logo/branding. Stock photos are allowed if needed, but I have uploaded some images of our church and would prefer those images to be used if possible. Any stock photos used should not include any people in the photos (scenery, nature, buildings, animals, etc. are fine).

The site will need 4 pages: Home, Support Us (Donate), Login, and Recording Library.

Page 1: Home
The home page should include the following sections:

- Navigation: Should include links to each section of the home page plus a "listen live" link which will take the user to a live-streaming site and a "support us" link which will take the user to a support/donate page.

- Announcements: Can be either a banner or some other design, but there needs to be some way for us to post announcements for visitors to see. I'm open for creative ideas in this section, but would like it not to take up a lot of room on the page.

- About Us: Should include address, service times (see attached document), and information about the church.

- Pastor Bio: A section that introduces our pastor and gives a short bio about our pastor. Would like this section to include a picture of our pastor. Somewhere in this section I would like to include this Bible reference: "And I will give you pastors according to mine heart, which shall feed you with knowledge and understanding. Jer 3:15 LPW"

- Articles of Faith (What We Believe): This should include several sub-sections each with a heading, body, and possibly 1 or more scripture references. I have attached a document to the brief that includes our articles of faith. Feel free to be creative with this section in how you lay these out and format them.

- Support Us: A small section that explains what kind of support someone can give and a link to a donation page. The link can say something like "Support Us" or "Donate Now".

- Contact form: A contact form that allows the visitor to send us a message. The contact form should ask for name, email, phone, and message.

- Footer: A footer that will be displayed on all pages of the site. This should include at a minimum a link to the home page (or a link to each individual section in the home page if you prefer), a link to "listen live", a link to "support us", a link to "contact us" (or you can put the contact form directly in the footer if you prefer), the address, and a "member login" link.

Page 2: Support Us
The donation page should include a form the visitor can fill out to make a donation. We will embed a third party form later. For this design, please just mock out the design with a basic form asking for name, phone, and email.

Page 3: Login
The recording library (detailed below) will require members to login with a shared numeric code before accessing the page. We need a design for a login screen. The screen should include navigation/footer just like all other pages, but the body of the login page will consist only of a form that asks the user to enter the access code and then a "login" button.

Page 4: Recording Library

The library page is a member-only page that will require a shared, numeric pass code to access. On this page, members will be able to access a filterable list of past sermons. The page by default should display most recent sermons, but should also include a search form that allows the member to filter the sermon list to find a particular sermon. The search form should allow the user to select a filter type (e.g. Speaker name, date, event, etc.) and type in a value to search. They should be able to add multiple filters and remove filters that have been added. Each sermon that is displayed in the result list should include basic information such as title, date, speaker, tags, etc. along with a download icon, and an embedded audio player where they can click a play button to stream it on-demand. Each sermon should also have clickable tags associated with it that can be used to find related sermons.
Updates

I have uploaded several images of our church. Feel free to incorporate these into your design if possible.

Target Market(s)

Church Members

Industry/Entity Type

Religion

Number of Pages Required

4 page

Font styles to use
Sans Serif

Colors

Designer to choose colors to be used in the design.

Requirements
Must have
• Must incorporate the logo (attached)
Nice to have
• Would like the design to incorporate pictures of our church (attached) instead of stock photos if possible.
Should not have
• Please avoid an overly cluttered design. Stock photos used should not include any people in the photos.

```html
<!DOCTYPE html>
<html lang="en">
<head>
<meta charset="utf-8">
<title>Donation – Cedar Hill Chapel</title>
<link rel="stylesheet" href="https://fonts.googleapis.com/css2?family=Open+Sans:wght@300;400;600&family=Cormorant+Garamond:wght@700&display=swap">
<style>
:root{
  --green-deep:#41611f;
  --green-soft:#85a96b;
  --ink:#1f1f1f;
  --muted:#6b6b6b;
  --field:#f4f4f4;
  --footer:#353535;
  --footer-tile:#3e3e3e;
  --white:#ffffff;
}
*{box-sizing:border-box;margin:0;padding:0}
html,body{width:823px;height:1200px;overflow:hidden}
body{position:relative;background:var(--white);font-family:"Open Sans",Arial,sans-serif;color:var(--ink)}

.site-header{position:absolute;left:0;top:0;width:823px;height:56px;background:var(--white)}
.brand{position:absolute;left:107px;top:20px;display:flex;align-items:center;gap:5px;color:var(--green-soft);font-size:11px;font-weight:400;letter-spacing:.5px}
.brand-square{width:9px;height:9px;background:var(--green-soft)}
.main-nav{position:absolute;top:22px;left:0;width:823px;font-size:9px;letter-spacing:.3px}
.main-nav a{position:absolute;color:var(--ink);text-decoration:none}
.main-nav a.is-current{color:var(--green-soft)}

.hero{position:absolute;left:0;top:56px;width:823px;height:171px;background:linear-gradient(90deg,#2e261b 0%,#5a4a33 30%,#8a6c45 50%,#5a4a33 70%,#2b2318 100%)}
.hero-title{position:absolute;left:170px;top:74px;font-family:"Cormorant Garamond",Georgia,serif;font-weight:700;font-size:25px;color:var(--white);line-height:1}
.hero-rule{position:absolute;left:107px;top:91px;width:52px;height:1px;background:var(--white)}
.breadcrumb{position:absolute;left:106px;top:143px;font-size:10.5px;color:var(--white);display:flex;gap:9px}

.donation-card{position:absolute;left:120px;top:272px;width:581px;height:586px;background:var(--white);box-shadow:0 2px 6px rgba(0,0,0,.08)}
.card-head{height:129px;background:var(--green-deep);position:relative}
.card-emblem{position:absolute;left:29px;top:14px;width:92px;height:101px;border-radius:50%;background:rgba(255,255,255,.85)}
.card-title{position:absolute;left:140px;top:44px;font-family:"Cormorant Garamond",Georgia,serif;font-weight:700;font-size:30px;color:var(--white);line-height:1}

.field-label{position:absolute;font-size:9.5px;color:var(--ink)}
.field{position:absolute;height:28px;background:var(--field);font-size:8.5px;font-weight:300;color:var(--muted);padding-left:8px;display:flex;align-items:center}
.hint{position:absolute;font-size:5px;color:var(--muted)}
.card-icon{margin-right:10px}
.comments{height:89px}
.donate-btn{position:absolute;left:221px;top:527px;width:131px;height:36px;background:var(--green-soft);color:var(--white);font-size:15.5px;display:flex;align-items:center;justify-content:center;border-radius:2px}

.site-footer{position:absolute;left:0;top:911px;width:823px;height:289px;background:var(--footer);text-align:center}
.footer-brand{position:absolute;left:0;width:823px;top:57px;display:flex;justify-content:center;align-items:center;gap:6px;color:var(--green-soft);font-size:14px}
.footer-brand .brand-square{width:11px;height:11px}
.footer-nav{position:absolute;top:115px;left:0;width:823px;display:flex;justify-content:center;gap:16px;font-size:9.5px;font-weight:600;color:var(--white)}
.footer-nav .sep{color:var(--green-soft);font-weight:400}
.social{position:absolute;top:148px;left:362px;display:flex;gap:10px}
.social span{width:26px;height:27px;background:var(--footer-tile)}
.call-label{position:absolute;top:191px;width:823px;font-size:15.5px;color:var(--green-soft)}
.call-number{position:absolute;top:214px;width:823px;font-size:22px;font-weight:600;color:var(--white)}
.legal{position:absolute;top:260px;width:823px;font-size:8px;font-weight:300;color:#d0d0d0}
</style>
</head>
<body>

<header class="site-header">
  <div class="brand"><span class="brand-square"></span>Cedar Hill Chapel</div>
  <nav class="main-nav">
    <a href="#" style="left:516px">HOME</a>
    <a href="#" style="left:590px">LIBRARY</a>
    <a href="#" class="is-current" style="left:663px">DONATION</a>
  </nav>
</header>

<section class="hero" role="img" aria-label="Interior of the church nave with pews and arched stained-glass windows">
  <span class="hero-rule"></span>
  <h1 class="hero-title">Donation</h1>
  <div class="breadcrumb"><span>Home</span><span>›</span><span>Donation</span></div>
</section>

<main class="donation-card">
  <div class="card-head">
    <div class="card-emblem" role="img" aria-label="Emblem of four open hands joined in a circle"></div>
    <h2 class="card-title">Donation Form</h2>
  </div>

  <span class="field-label" style="left:15px;top:152px">Full Name</span>
  <div class="field" style="left:15px;top:172px;width:270px"></div>
  <div class="field" style="left:295px;top:172px;width:271px"></div>
  <span class="hint" style="left:17px;top:203px">First Name</span>
  <span class="hint" style="left:297px;top:203px">Last Name</span>

  <span class="field-label" style="left:15px;top:220px">Email</span>
  <span class="field-label" style="left:296px;top:220px">Phone</span>
  <div class="field" style="left:15px;top:239px;width:270px">ex: myname@example.com</div>
  <div class="field" style="left:295px;top:239px;width:271px"></div>

  <span class="field-label" style="left:15px;top:282px">Card Details:</span>
  <div class="field" style="left:15px;top:301px;width:270px">First Name</div>
  <div class="field" style="left:295px;top:301px;width:271px">Last Name</div>

  <div class="field" style="left:15px;top:346px;width:270px">
    <svg class="card-icon" width="20" height="14" viewBox="0 0 20 14" aria-hidden="true"><rect width="20" height="14" rx="1.5" fill="#222"/><rect y="3" width="20" height="2.5" fill="#f4f4f4"/><rect x="2" y="9" width="4" height="1.5" fill="#f4f4f4"/><rect x="7" y="9" width="3" height="1.5" fill="#f4f4f4"/></svg>
    Card Number
  </div>
  <div class="field" style="left:295px;top:346px;width:136px">MM/YY</div>
  <div class="field" style="left:441px;top:346px;width:124px">CVV</div>

  <span class="field-label" style="left:15px;top:390px">Comments</span>
  <div class="field comments" style="left:15px;top:410px;width:550px"></div>

  <div class="donate-btn">Donate Now</div>
</main>

<footer class="site-footer">
  <div class="footer-brand"><span class="brand-square"></span>Cedar Hill Chapel</div>
  <nav class="footer-nav">
    <span>HOME</span><span class="sep">|</span><span>LIBRARY</span><span class="sep">|</span><span>DONATION</span>
  </nav>
  <div class="social" aria-label="Social links"><span></span><span></span><span></span></div>
  <p class="call-label">Call us</p>
  <p class="call-number">555.010.2468</p>
  <p class="legal">© 2023 Cedar Hill Chapel. All rights reserved. Privacy Policy</p>
</footer>

</body>
</html>
```